Kelvor Engineers: Why you should hire us keepsake

New design. Open to plastic cards. We are an engineering firm that designs cell phone towers and commercial buildings. Please check out our website www.kelvorstruct.com for more details. We want people to remember our card and for it to be useful if possible. We want the same look and feel on these cards to be translated to other marketing material we may need such as brochures.

Target Market(s)

Architects, Developers and Telecommunication Carriers

Industry/Entity Type

Engineering

Contact Information for Business Card

Card with our company colors, logo, and innovative design with elements related to our industry.

Font styles to use
Sans Serif

Colors
9bcb3c
abd036
0255a3

Requirements
Must have
• Sleek and hip design
Nice to have
• Bright lime green and navy coloring that pops with an innovative design.
Should not have
• A basic and boring design

```html
<!DOCTYPE html>
<html lang="en">
<head>
<meta charset="utf-8">
<title>Kelvor Engineers – Business Card</title>
<link href="https://fonts.googleapis.com/css2?family=Roboto:wght@400;700;900&display=swap" rel="stylesheet">
<style>
  :root {
    --navy: #022a55;
    --lime: #1ee61e;
    --paper: #f2f2f2;
    --bg: #dcdcdc;
    --ink-light: #ffffff;
  }
  * { margin: 0; padding: 0; box-sizing: border-box; }
  html, body { width: 1200px; height: 990px; overflow: hidden; }
  body {
    background: var(--bg);
    font-family: "Roboto", Arial, sans-serif;
    position: relative;
  }
  .card {
    position: absolute;
    left: 290px;
    width: 620px;
    height: 343px;
    overflow: hidden;
  }
  .card--front { top: 124px; background: var(--paper); }
  .card--back { top: 524px; background: var(--navy); }

  /* front: navy info panel */
  .info-panel {
    position: absolute; left: 0; top: 0;
    width: 320px; height: 100%;
    background: var(--navy);
    color: var(--ink-light);
    text-align: right;
  }
  .accent-stripe {
    position: absolute; left: 320px; top: 0;
    width: 6px; height: 100%;
    background: var(--lime);
  }
  .accent-notch { position: absolute; left: 306px; top: 68px; }
  .person-name {
    position: absolute; right: 49px; top: 70px;
    font-size: 19px; font-weight: 700; letter-spacing: 0.2px;
  }
  .address {
    position: absolute; right: 49px; top: 180px;
    font-size: 14px; line-height: 18px;
  }
  .address .discipline { color: var(--lime); }
  .contacts {
    position: absolute; right: 49px; top: 256px;
    font-size: 14px; line-height: 18.5px;
    list-style: none;
  }
  .contacts li { display: flex; justify-content: flex-end; align-items: center; gap: 7px; }
  .contacts svg { width: 13px; height: 12px; flex: none; }

  /* front: white side */
  .brand-name {
    color: var(--lime);
    font-weight: 900;
    line-height: 1;
    position: absolute;
  }
  .card--front .brand-name {
    left: 372px; top: 62px;
    font-size: 36px;
    letter-spacing: -0.5px;
  }
  .web {
    position: absolute;
    font-size: 12px;
    letter-spacing: 5px;
    white-space: nowrap;
  }
  .web b { font-weight: 700; }
  .card--front .web { left: 372px; top: 290px; color: var(--navy); }
  .card--front .web b { color: var(--navy); }

  /* back */
  .card--back .brand-name {
    left: 0; right: 0; top: 140px;
    text-align: center;
    font-size: 50px;
    letter-spacing: -0.5px;
  }
  .card--back .web {
    left: 0; right: 0; top: 282px;
    text-align: center;
    color: var(--ink-light);
    font-size: 13px;
    letter-spacing: 6px;
  }
  .card--back .web b { color: var(--lime); }
</style>
</head>
<body>

  <section class="card card--front" aria-label="Business card front">
    <div class="info-panel">
      <p class="person-name">DANA WHITLOW PIERCE</p>
      <p class="address">
        <span class="discipline">MULTI-DISCIPLINE ENGINEERING</span><br>
        2400 Marlowe Ridge Pkwy<br>
        Suite 310 Alderton, GA 30190
      </p>
      <ul class="contacts">
        <li>706.555.0142
          <svg viewBox="0 0 12 12" aria-hidden="true"><rect x="3" y="0.8" width="6.5" height="10.4" rx="1.3" fill="none" stroke="#1ee61e" stroke-width="1.4"/></svg>
        </li>
        <li>678.555.0193
          <svg viewBox="0 0 12 12" aria-hidden="true"><path d="M3 1 L5 1 L5.8 3.6 L4.6 4.6 Q5.6 7 7.6 8 L8.6 6.8 L11 7.6 L11 9.8 Q10 11.2 8.4 11 Q2.4 9.4 1.2 3 Q1.2 1.6 3 1 Z" fill="#1ee61e"/></svg>
        </li>
        <li>dpierce@kelvorstruct.com
          <svg viewBox="0 0 14 12" aria-hidden="true"><rect x="0.5" y="1.5" width="13" height="9" fill="#1ee61e"/><path d="M0.5 1.5 L7 6.8 L13.5 1.5" fill="none" stroke="#022a55" stroke-width="1.2"/></svg>
        </li>
      </ul>
    </div>
    <div class="accent-stripe"></div>
    <svg class="accent-notch" width="16" height="40" viewBox="0 0 16 40" aria-hidden="true"><polygon points="16,0 0,20 16,40" fill="#1ee61e"/></svg>

    <p class="brand-name">Kelvor<br>Engineers</p>
    <p class="web">www.<b>kelvorstruct</b>.com</p>
  </section>

  <section class="card card--back" aria-label="Business card back">
    <p class="brand-name">Kelvor Engineers</p>
    <p class="web">www.<b>kelvorstruct</b>.com</p>
  </section>

</body>
</html>
```